DANCE STUDIO RECITAL FLYER DESIGN 2022

I am looking for a flyer for a dance recital that encapsulates the theme of the flyer. The rhetorical answer to "Where the River Bends Home..." is Hold Me Near but I would like this to be inferred in the design of the flyer. I am looking for something uplifting and positive through the design...I don't know what I am looking for but it needs to be vibrant, heartwarming, and emotional...maybe the world can be dipped in a heart or something with butterflies???

Here are the details...

Brightwing Dance Studio presents
Our 11th Annual Recital, "Where The River Bends Home..."
Saturday, June 25, at 4 pm
Kestrel Ridge High School 31857 Marlow Road
Larkmoor, MN 48291

```html
<!DOCTYPE html>
<html lang="en">
<head>
<meta charset="UTF-8">
<title>Brightwing Dance Studio – 11th Annual Recital</title>
<link href="https://fonts.googleapis.com/css2?family=Oswald:wght@400;500;700&family=Cinzel:wght@700&display=swap" rel="stylesheet">
<style>
  :root {
    --maroon: #7c1519;
    --maroon-deep: #5e0e12;
    --gold: #f7c41c;
    --white: #ffffff;
    --photo-light: #c9a9a4;
    --photo-mid: #9a4e52;
  }
  * { margin: 0; padding: 0; box-sizing: border-box; }
  html, body { width: 784px; height: 1200px; overflow: hidden; background: #ececec; }
  .flyer {
    position: relative;
    width: 784px; height: 1200px;
    background: linear-gradient(160deg, var(--maroon) 0%, var(--maroon) 55%, var(--maroon-deep) 100%);
    font-family: 'Oswald', sans-serif;
    color: var(--white);
    overflow: hidden;
  }
  .flyer__lines { position: absolute; inset: 0; }
  .dancer-photo {
    position: absolute; right: 0; top: 0;
    width: 420px; height: 1130px;
    background: radial-gradient(ellipse at 50% 45%, var(--photo-light) 0%, var(--photo-mid) 45%, rgba(124,21,25,0) 75%);
  }
  .studio-mark {
    position: absolute; left: 40px; top: 30px;
    width: 230px; height: 150px;
    background: var(--white);
    display: flex; flex-direction: column; align-items: center; justify-content: center; gap: 10px;
  }
  .studio-mark__dot { width: 26px; height: 26px; border-radius: 50%; background: var(--maroon); }
  .studio-mark__name {
    font-family: 'Cinzel', serif; font-weight: 700; font-size: 21px;
    color: var(--maroon); text-align: center; line-height: 1.15;
  }
  .presents { position: absolute; left: 44px; top: 212px; font-size: 17px; letter-spacing: 2px; font-weight: 500; }
  .recital-pill {
    position: absolute; left: 40px; top: 244px;
    border: 2px solid var(--white); border-radius: 40px;
    padding: 6px 22px; font-size: 26px; font-weight: 500; letter-spacing: 1px;
  }
  .recital-pill em { font-style: normal; color: var(--gold); font-weight: 700; font-size: 34px; }
  .recital-pill sup { font-size: 16px; }
  .title { position: absolute; left: 40px; top: 320px; font-weight: 700; line-height: 0.98; text-transform: uppercase; }
  .title__line { display: block; font-size: 86px; }
  .title__line--accent { color: var(--gold); font-size: 150px; line-height: 0.95; }
  .date { position: absolute; left: 40px; top: 690px; display: flex; align-items: center; gap: 12px; }
  .date__day { font-size: 96px; font-weight: 700; color: var(--gold); line-height: 1; }
  .date__time {
    background: var(--white); color: var(--maroon);
    font-weight: 700; font-size: 22px; line-height: 1.05;
    padding: 8px 6px; text-align: center;
  }
  .weekday { position: absolute; left: 40px; top: 800px; font-size: 74px; font-weight: 700; letter-spacing: 1px; }
  .venue { position: absolute; left: 40px; top: 915px; display: flex; gap: 12px; align-items: flex-start; }
  .venue__text { color: var(--gold); font-size: 24px; font-weight: 500; line-height: 1.3; }
  .website { position: absolute; left: 40px; top: 1040px; font-size: 18px; letter-spacing: 0.5px; }
  .footer-band { position: absolute; left: 0; bottom: 0; width: 100%; height: 40px; background: var(--white); }
</style>
</head>
<body>
  <main class="flyer">
    <svg class="flyer__lines" width="784" height="1200" viewBox="0 0 784 1200" aria-hidden="true">
      <g stroke="#ffffff" stroke-opacity="0.07" stroke-width="2" fill="none">
        <path d="M380 1160 Q600 700 784 520"/>
        <path d="M420 1160 Q620 760 784 600"/>
        <path d="M460 1160 Q650 820 784 680"/>
        <path d="M500 1160 Q680 880 784 760"/>
      </g>
    </svg>

    <div class="dancer-photo" role="img" aria-label="Photo of a ballerina en pointe in a pink tutu, arms raised"></div>

    <div class="studio-mark">
      <span class="studio-mark__dot"></span>
      <span class="studio-mark__name">Brightwing<br>Dance Studio</span>
    </div>

    <p class="presents">PRESENTS</p>
    <p class="recital-pill">OUR <em>11<sup>th</sup></em> ANNUAL RECITAL</p>

    <h1 class="title">
      <span class="title__line">Where the</span>
      <span class="title__line title__line--accent">River</span>
      <span class="title__line">Bends Home</span>
    </h1>

    <div class="date">
      <span class="date__day">25 JUNE</span>
      <span class="date__time">4<br>PM</span>
    </div>
    <p class="weekday">SATURDAY</p>

    <div class="venue">
      <svg width="22" height="30" viewBox="0 0 22 30" aria-hidden="true">
        <path d="M11 0C5 0 0 5 0 11c0 8 11 19 11 19s11-11 11-19C22 5 17 0 11 0z" fill="#f7c41c"/>
        <circle cx="11" cy="11" r="4" fill="#7c1519"/>
      </svg>
      <p class="venue__text">Kestrel Ridge High School 31857 Marlow Road<br>Larkmoor, MN 48291</p>
    </div>

    <p class="website">www.brightwingstudio.org</p>
    <div class="footer-band"></div>
  </main>
</body>
</html>
```